Business Card Design

We need a business card designed for our new company. Prefer a black card with white logo & writing.

Contact Information for Business Card

Ted Galloway, address: 7-4812 Fernhollow Road, Abbotsford, BC, V3K 8R2, Office Phone: 604-712-3390, Cell: 604-947-2164, Email: ted@resinworkshub.ca

Colors

Designer to choose only greyscale colors for use in the design.

```html
<!DOCTYPE html>
<html lang="en">
<head>
<meta charset="utf-8">
<title>Resinworks Hub – Business Card</title>
<link rel="stylesheet" href="https://fonts.googleapis.com/css2?family=Montserrat:wght@400;500;700;800&display=swap">
<style>
  :root {
    --backdrop: #1e1e1e;
    --card: #000000;
    --ink: #ffffff;
    --grey-light: #9a9a9c;
    --grey-dark: #58585a;
  }
  * { margin: 0; padding: 0; box-sizing: border-box; }
  html, body { width: 1200px; height: 900px; overflow: hidden; }
  body {
    background: var(--backdrop);
    font-family: "Montserrat", Arial, sans-serif;
    color: var(--ink);
    position: relative;
  }
  .card {
    position: absolute;
    left: 341px;
    width: 518px;
    height: 296px;
    background: var(--card);
    overflow: hidden;
  }
  .card--front { top: 141px; }
  .card--back { top: 463px; }
  .card__graphic {
    position: absolute;
    top: 0;
    width: 518px;
    height: 296px;
    left: 0;
  }
  .wordmark {
    position: absolute;
    font-weight: 800;
    color: var(--ink);
    white-space: nowrap;
  }
  .card--front .wordmark {
    left: 27px;
    top: 24px;
    font-size: 29px;
    letter-spacing: 0.5px;
  }
  .contact {
    position: absolute;
    left: 27px;
    top: 101px;
    font-size: 13px;
    line-height: 18px;
    font-weight: 400;
  }
  .contact__name {
    font-size: 17px;
    font-weight: 700;
    line-height: 20px;
    letter-spacing: 0.3px;
  }
  .contact__title { margin-bottom: 13px; }
  .contact__address { margin-bottom: 12px; }
  .contact__list { list-style: none; }
  .contact__list li { display: flex; align-items: center; gap: 6px; }
  .contact__list svg { width: 12px; height: 12px; flex: none; }
  .card--back .wordmark {
    left: 360px;
    top: 148px;
    transform: translate(-50%, -50%);
    font-size: 25px;
    letter-spacing: 0.5px;
  }
</style>
</head>
<body>

<section class="card card--front" aria-label="Card front">
  <svg class="card__graphic" viewBox="0 0 518 296" aria-hidden="true">
    <circle cx="517" cy="147" r="155" fill="var(--ink)"/>
  </svg>
  <svg class="card__graphic" viewBox="0 0 518 296" role="img" aria-label="Layered stripe graphic in greys">
    <defs>
      <linearGradient id="stripeFront" x1="0" y1="0" x2="0" y2="1">
        <stop offset="0" stop-color="var(--grey-light)"/>
        <stop offset="1" stop-color="var(--grey-dark)"/>
      </linearGradient>
    </defs>
    <rect x="372" y="110" width="146" height="90" fill="url(#stripeFront)"/>
  </svg>
  <div class="wordmark">RESINWORKS</div>
  <div class="contact">
    <div class="contact__name">TED GALLOWAY</div>
    <div class="contact__title">President</div>
    <div class="contact__address">7-4812 Fernhollow Road<br>Abbotsford, BC, V3K 8R2</div>
    <ul class="contact__list">
      <li><svg viewBox="0 0 24 24"><path fill="var(--ink)" d="M6.6 10.8a15 15 0 0 0 6.6 6.6l2.2-2.2c.3-.3.7-.4 1-.2 1.1.4 2.3.6 3.6.6.6 0 1 .4 1 1V20c0 .6-.4 1-1 1A17 17 0 0 1 3 4c0-.6.4-1 1-1h3.5c.6 0 1 .4 1 1 0 1.3.2 2.5.6 3.6.1.3 0 .7-.2 1z"/></svg>604-712-3390</li>
      <li><svg viewBox="0 0 24 24"><rect x="6" y="2" width="12" height="20" rx="2" fill="none" stroke="var(--ink)" stroke-width="2"/><circle cx="12" cy="18.5" r="1.2" fill="var(--ink)"/></svg>604-947-2164</li>
      <li><svg viewBox="0 0 24 24"><path fill="var(--ink)" d="M2 5h20v14H2z"/><path fill="none" stroke="var(--card)" stroke-width="2" d="M2 6l10 7 10-7"/></svg>ted@resinworkshub.ca</li>
      <li><svg viewBox="0 0 24 24" fill="none" stroke="var(--ink)" stroke-width="1.8"><circle cx="12" cy="12" r="10"/><ellipse cx="12" cy="12" rx="4.5" ry="10"/><path d="M2 12h20M4 7h16M4 17h16"/></svg>resinworkshub.ca</li>
    </ul>
  </div>
</section>

<section class="card card--back" aria-label="Card back">
  <svg class="card__graphic" viewBox="0 0 518 296" aria-hidden="true">
    <circle cx="0" cy="148" r="155" fill="var(--ink)"/>
  </svg>
  <svg class="card__graphic" viewBox="0 0 518 296" role="img" aria-label="Layered stripe graphic in greys">
    <defs>
      <linearGradient id="stripeBack" x1="0" y1="0" x2="0" y2="1">
        <stop offset="0" stop-color="var(--grey-light)"/>
        <stop offset="1" stop-color="var(--grey-dark)"/>
      </linearGradient>
    </defs>
    <rect x="0" y="136" width="150" height="90" fill="url(#stripeBack)"/>
  </svg>
  <div class="wordmark">RESINWORKS HUB</div>
</section>

</body>
</html>
```